Strategy and Technology Consulting - Our Story and Values Page

Interior Page design – Our History and Our Values

Our homepage has been designed and we are looking for a design for one of the interior pages. This interior page tells the story of Our History and Our Values

Because the homepage has been designed, we would like this interior page to reflect the design of the homepage without being a mirror image of the homepage.

This site will be implemented in WordPress using the Elementor framework.

Font: Poppins medium and Poppins dark
Illustrations: Our homepage illustrations were designed by “Brelin 1974” on Quillmark. Compatible original or stock illustrations are welcome. Stock photography is also welcome. Brelin is also available through Brelin Tosamek on Ravolo

Uploaded Files
• Homepage design – this is the design we will use for our homepage. Contest entries should reflect this basic style but should be distinctly different from the homepage.
• Our History and Our Values – Wireframe – the basic layout of the page we are looking for.
• Our History and Our Values – Word document with the text supporting the wireframe.
• Color Palette – please use colors compatible with the palette attached.

Our Story - timeline
There is a timeline element in the wireframe. The wireframe displays this as a series of chevrons (arrows), but it does not need to be. Creativity in display of the timeline is appreciated.

Our Values
If you look at the Word document, you will see that there are a lot of words on the page. The winning design will present the information in a way that engages the user without overwhelming them with too much to read. For example, they may click on a value and see more information.

Target Market(s)

CIO's and Technology Executives

Number of Pages Required

1 page

Font styles to use
Sans Serif
Other font styles liked:
• Poppin

Requirements
Must have
• A timeline element, all of our values
Nice to have
• Clever timeline display

```html
<!DOCTYPE html>
<html lang="en">
<head>
<meta charset="utf-8">
<title>Veltrana – Our Story &amp; Values</title>
<link href="https://fonts.googleapis.com/css2?family=Poppins:wght@400;500;600;700;800&display=swap" rel="stylesheet">
<style>
:root{
  --navy:#3d4660;
  --navy-dark:#353d53;
  --navy-deep:#2f3649;
  --yellow:#f2b81e;
  --blue:#3a5fb0;
  --blob:#e6ecfb;
  --text:#555a66;
  --heading:#3b4257;
  --grey-bg:#f1f1f3;
  --white:#ffffff;
}
*{margin:0;padding:0;box-sizing:border-box}
html,body{width:1200px;height:4241px;overflow:hidden}
body{position:relative;background:var(--white);font-family:'Poppins',sans-serif;color:var(--text)}
.abs{position:absolute}

/* header */
.brand{left:92px;top:22px;font-size:44px;font-weight:500;color:#8b8f99;letter-spacing:.5px}
.nav{left:542px;top:36px;display:flex;gap:26px;align-items:center;font-size:12.5px;font-weight:600;color:var(--heading)}
.nav .home{width:14px;height:13px}
.nav span::after{content:" ⌄";font-size:11px}
.btn{background:var(--yellow);color:var(--white);font-weight:700;font-size:12px;border-radius:30px;text-align:center;letter-spacing:.3px}
.btn-contact{left:979px;top:28px;width:132px;height:36px;line-height:36px}

/* section titles */
.section-title{width:1200px;text-align:center;font-size:32px;font-weight:700;color:var(--heading)}

/* timeline */
.story-wave{left:0;top:230px;width:1200px;height:340px}
.tl-card{top:191px;width:301px;height:281px;background:var(--white);box-shadow:0 4px 22px rgba(0,0,0,.08)}
.tl-tag{position:absolute;left:-17px;top:20px;height:41px;padding:0 44px 0 37px;background:var(--navy);color:var(--white);font-size:19px;font-weight:600;line-height:41px;clip-path:polygon(0 0,100% 0,86% 100%,0 100%)}
.tl-tag::before{content:"";position:absolute;left:0;bottom:-10px;width:17px;height:10px;background:var(--navy-deep)}
.tl-list{position:absolute;left:20px;top:78px;right:20px;list-style:none;font-size:16px;line-height:20px;color:var(--heading)}
.tl-list li{position:relative;padding-left:20px;margin-bottom:10px}
.tl-list li::before{content:"";position:absolute;left:2px;top:5px;width:9px;height:9px;border-radius:50%;background:var(--yellow)}
.tl-list li.sub{padding-left:20px;margin-bottom:6px}
.tl-list li.sub::before{width:4px;height:4px;top:8px;left:10px;background:var(--heading)}
.tl-link{top:324px;height:16px}

/* values */
.value-text{width:490px}
.value-text h3{font-size:28px;font-weight:700;color:var(--heading);line-height:36px;margin-bottom:20px}
.value-text p{font-size:15.5px;line-height:27.5px}
.illus{border-radius:46% 54% 50% 50% / 52% 48% 52% 48%;background:radial-gradient(circle at 50% 55%,var(--blob) 0 62%,#f4f6fc 63%,transparent 64%)}
.illus::after{content:"";position:absolute;left:38%;top:14%;width:24%;height:74%;border-radius:40px 40px 6px 6px;background:linear-gradient(180deg,#5d6578,#2f3649);opacity:.18}

/* newsletter & footer */
.footer-wave{left:0;top:3500px;width:1200px;height:320px}
.footer-body{left:0;top:3818px;width:1200px;height:363px;background:linear-gradient(180deg,var(--navy) 0%,#3e4862 100%)}
.newsletter{left:137px;top:3531px;width:925px;height:205px;border-radius:103px;background:var(--yellow)}
.newsletter h2{position:absolute;left:80px;top:62px;font-size:32px;font-weight:800;color:var(--white)}
.newsletter p{position:absolute;left:80px;top:112px;width:420px;font-size:14px;line-height:19px;color:var(--white)}
.nl-field{position:absolute;left:549px;top:84px;width:319px;height:44px;border-radius:22px;background:var(--white);font-size:12px;color:#8b8f99;line-height:44px;padding-left:44px}
.nl-field svg.mail{position:absolute;left:22px;top:16px}
.nl-send{position:absolute;right:4px;top:4px;width:36px;height:36px;border-radius:50%;background:#a9b1c4}

.f-brand{left:123px;top:3922px;font-size:62px;font-weight:500;color:#a9b1c4;letter-spacing:1px}
.socials{left:177px;top:3995px;display:flex;gap:13px}
.socials span{width:37px;height:37px;border-radius:50%;background:#5b6581;border:1px solid #7a84a0}
.btn-footer{left:214px;top:4060px;width:132px;height:36px;line-height:36px}
.f-col h4{font-size:19px;font-weight:700;color:var(--white);margin-bottom:20px}
.f-col ul{list-style:none;font-size:12.5px;color:#e4e7ef}
.f-col li{height:31px}
.f-col li::before{content:"›";margin-right:8px}
.contact-item{position:relative;padding-left:22px;font-size:12.5px;line-height:17px;color:#e4e7ef;margin-bottom:20px}
.contact-item svg{position:absolute;left:0;top:2px}
.copyright{left:0;top:4181px;width:1200px;height:60px;background:var(--navy-deep);color:var(--white);font-size:13px;text-align:center;line-height:60px}
.chat{left:1133px;top:4168px;width:46px;height:46px;border-radius:50%;background:var(--yellow)}
</style>
</head>
<body>

<!-- Header -->
<div class="abs brand">Veltrana</div>
<nav class="abs nav">
  <svg class="home" viewBox="0 0 14 13"><path d="M7 0L0 6h2v7h4V9h2v4h4V6h2z" fill="#8b93a8"/></svg>
  <span>ABOUT US</span><span>SERVICES</span><span>INSIGHTS</span><span>JOIN US</span>
</nav>
<div class="abs btn btn-contact">CONTACT US</div>

<!-- Our Story -->
<h1 class="abs section-title" style="top:116px">Our Story</h1>
<svg class="abs story-wave" viewBox="0 0 1200 340" preserveAspectRatio="none">
  <path d="M0 150 C200 260 420 300 620 250 C820 200 1000 120 1200 60 L1200 340 L0 340Z" fill="var(--grey-bg)"/>
</svg>

<div class="abs tl-card" style="left:91px">
  <div class="tl-tag">2017 – 2019</div>
  <ul class="tl-list">
    <li>Growth Strategy Focus</li>
    <li>Consistent, Modest Growth</li>
    <li>Preliminary Focus on Technology</li>
    <li>Eureka! Implementing strategy is hard .</li>
  </ul>
</div>
<div class="abs tl-card" style="left:449px">
  <div class="tl-tag">2020 – 2021</div>
  <ul class="tl-list">
    <li>Pandemic Pauses Growth</li>
    <li>Rethinking :</li>
    <li class="sub">The Business Model</li>
    <li class="sub">The Delivery Model</li>
  </ul>
</div>
<div class="abs tl-card" style="left:815px">
  <div class="tl-tag">2022 &amp; Onward</div>
  <ul class="tl-list">
    <li>Leadership Team for Focus on Essential Areas</li>
    <li>Rapid Growth</li>
    <li>Customer Success</li>
  </ul>
</div>
<svg class="abs tl-link" style="left:382px;width:78px" viewBox="0 0 78 16"><line x1="9" y1="8" x2="69" y2="8" stroke="#3d4660" stroke-dasharray="2 2"/><circle cx="8" cy="8" r="6.5" fill="#fff" stroke="#3d4660"/><circle cx="70" cy="8" r="6.5" fill="#fff" stroke="#3d4660"/></svg>
<svg class="abs tl-link" style="left:740px;width:78px" viewBox="0 0 78 16"><line x1="9" y1="8" x2="69" y2="8" stroke="#3d4660" stroke-dasharray="2 2"/><circle cx="8" cy="8" r="6.5" fill="#fff" stroke="#3d4660"/><circle cx="70" cy="8" r="6.5" fill="#fff" stroke="#3d4660"/></svg>

<!-- Our Values -->
<h2 class="abs section-title" style="top:561px">Our Values</h2>

<div class="abs value-text" style="left:92px;top:728px">
  <h3>The Value of Every Human.<br>Regardless.</h3>
  <p>Each person's unique experiences and perspectives add vibrant hues to the tapestry of our shared existence. In a world where diversity paints the canvas of humanity, true beauty is found in recognizing the inherent and incalculable value of every human being.</p>
</div>
<div class="abs illus" style="left:662px;top:639px;width:430px;height:390px" role="img" aria-label="Illustration of a businessman with a megaphone surrounded by people and idea icons"></div>

<div class="abs illus" style="left:92px;top:1032px;width:430px;height:387px" role="img" aria-label="Illustration of two colleagues shaking hands over puzzle pieces with growth charts"></div>
<div class="abs value-text" style="left:634px;top:1112px">
  <h3>Collaboration</h3>
  <p>Collaboration in work transforms individual endeavors into symphonies of collective achievement. Through collaboration, diverse talents converge, fostering a rich exchange of ideas that amplifies creativity, accelerates progress, and brings forth solutions beyond what a single mind could conceive.</p>
</div>

<div class="abs value-text" style="left:92px;top:1544px">
  <h3>Passion</h3>
  <p>Passion infuses our work with energy, transforming routine tasks into opportunities for creativity and innovation. Fueled by passion, individuals become unstoppable forces, driven to overcome challenges and achieve remarkable outcomes that benefit them and inspire those around them</p>
</div>
<div class="abs illus" style="left:657px;top:1424px;width:430px;height:395px" role="img" aria-label="Illustration of a woman climbing with a flag along rising arrows before a city skyline"></div>

<div class="abs illus" style="left:77px;top:1830px;width:494px;height:376px" role="img" aria-label="Illustration of two people working on laptops around a circular arrow, stopwatch and target"></div>
<div class="abs value-text" style="left:634px;top:1924px">
  <h3>Excellence</h3>
  <p>Excellence isn't a destination; it's a continuous journey of refinement and growth. Striving for excellence cultivates a culture of continuous improvement, fostering innovation, credibility, and a lasting impact that resonates far beyond the immediate task.</p>
</div>

<div class="abs value-text" style="left:92px;top:2308px">
  <h3>Tenacity</h3>
  <p>Tenacity is the unwavering anchor that keeps us grounded amidst adversity, propelling us forward when faced with obstacles. The resilience to persist, adapt, and learn from setbacks leads to the mastery of skills and the fulfillment of ambitious goals.</p>
</div>
<div class="abs illus" style="left:662px;top:2206px;width:430px;height:387px" role="img" aria-label="Illustration of a man with a flag standing on a mountain peak"></div>

<div class="abs illus" style="left:92px;top:2606px;width:443px;height:398px" role="img" aria-label="Illustration of a man carrying a large puzzle piece among puzzle blocks"></div>
<div class="abs value-text" style="left:634px;top:2718px">
  <h3>Solution Mindset</h3>
  <p>A solution mindset is the compass that directs our focus from problems to possibilities. It empowers us to navigate challenges with a proactive mindset, igniting a journey of exploration and innovation that not only resolves issues but also paves the way for continuous growth and success.</p>
</div>

<div class="abs value-text" style="left:92px;top:3135px">
  <h3>Generosity</h3>
  <p>Generosity creates a virtuous cycle of goodwill, fostering a sense of unity and shared purpose among colleagues. By freely sharing knowledge, support, and resources, we uplift those around us and contribute to a collaborative environment where collective achievements flourish.</p>
</div>
<div class="abs illus" style="left:662px;top:2999px;width:430px;height:425px" role="img" aria-label="Illustration of two businessmen shaking hands with coins and plants"></div>

<!-- Newsletter & Footer -->
<svg class="abs footer-wave" viewBox="0 0 1200 320" preserveAspectRatio="none">
  <path d="M0 40 C120 10 200 120 330 190 C460 260 600 250 760 210 C900 175 1050 140 1200 50 L1200 320 L0 320Z" fill="#dcdde2"/>
  <path d="M0 50 C120 20 200 130 330 205 C460 275 600 265 760 225 C900 190 1050 155 1200 65 L1200 320 L0 320Z" fill="var(--navy)"/>
</svg>
<div class="abs footer-body"></div>

<div class="abs newsletter">
  <h2>Subscribe Our Newsletter</h2>
  <p>Subscribe our newsletter to receive the latest news and exclusive offers every week, No spam.</p>
  <div class="nl-field">
    <svg class="mail" width="13" height="10" viewBox="0 0 13 10"><rect width="13" height="10" rx="1" fill="#8b93a8"/><path d="M0 1l6.5 4.5L13 1" stroke="#fff" fill="none"/></svg>
    Enter email address
    <div class="nl-send"><svg width="36" height="36" viewBox="0 0 36 36"><path d="M11 18l14-7-5 15-2-6z" fill="#fff"/></svg></div>
  </div>
</div>

<div class="abs f-brand">Veltrana</div>
<div class="abs socials"><span></span><span></span><span></span><span></span></div>
<div class="abs btn btn-footer">CONTACT US</div>

<div class="abs f-col" style="left:491px;top:3892px">
  <h4>Quick links</h4>
  <ul><li>Home</li><li>About Us</li><li>Services</li><li>Insights</li><li>Join Us</li><li>Contact Us</li></ul>
</div>
<div class="abs f-col" style="left:668px;top:3892px">
  <h4>Our Services</h4>
  <ul><li>Business Transformation</li><li>ERP Implementations</li><li>ERP Solutions</li><li>BI and Data</li><li>Building the Right Team...</li></ul>
</div>
<div class="abs f-col" style="left:899px;top:3892px;width:220px">
  <h4>Contact info</h4>
  <div class="contact-item"><svg width="13" height="10" viewBox="0 0 13 10"><rect width="13" height="10" rx="1" fill="var(--yellow)"/><path d="M0 1l6.5 4.5L13 1" stroke="#3d4660" fill="none"/></svg>Email:<br>hello@veltrana-mail.com</div>
  <div class="contact-item"><svg width="12" height="12" viewBox="0 0 12 12"><path d="M2 0l3 3-1.5 2a7 7 0 003.5 3.5L9 7l3 3-2 2C5 12 0 7 0 2z" fill="var(--yellow)"/></svg>Phone:<br>+44 100 555 0199</div>
  <div class="contact-item"><svg width="10" height="14" viewBox="0 0 10 14"><path d="M5 0a5 5 0 015 5c0 4-5 9-5 9S0 9 0 5a5 5 0 015-5z" fill="var(--yellow)"/><circle cx="5" cy="5" r="2" fill="#3d4660"/></svg>Location:<br>Some address line goes<br>here city name</div>
</div>

<div class="abs copyright">© Veltrana Design 2023, All Rights Reserved</div>
<div class="abs chat"><svg width="46" height="46" viewBox="0 0 46 46"><path d="M13 14h20a3 3 0 013 3v10a3 3 0 01-3 3H20l-6 5v-5h-1a3 3 0 01-3-3V17a3 3 0 013-3z" fill="#fff"/></svg></div>

</body>
</html>
```